Business Card Design Project

I require a business card with the following information on them for various different people;
name
m:
f:
e:
I have a logo already and will attached that. We are in the construction industry. I require something clean and simple but eye catching at the same time. You can use another colour with our logo if you like and you can style the logo as well if you wish. I am open.
Also it needs to be front and back design.
Industry/Entity Type
Construction
Requirements
Must have
- Logo, name, mobile, fax and email address.
Front and back design

```html
<!DOCTYPE html>
<html lang="en">
<head>
<meta charset="utf-8">
<title>Northgate Developments – Business Cards</title>
<link rel="stylesheet" href="https://fonts.googleapis.com/css2?family=Mulish:wght@400;500;700&display=swap">
<style>
  :root {
    --page-bg: #ece9e4;
    --card-white: #ffffff;
    --brand-green: #4fae46;
    --brand-green-light: #b9de5c;
    --brand-grey: #4a4a4c;
    --ink: #222222;
    --ink-soft: #555555;
    --band-grey: #d6d6d8;
  }
  * { box-sizing: border-box; margin: 0; padding: 0; }
  html, body {
    width: 1200px; height: 757px; overflow: hidden;
    background: var(--page-bg);
    font-family: "Mulish", Arial, sans-serif;
  }
  .canvas { position: relative; width: 1200px; height: 757px; }

  .card {
    position: absolute; width: 513px; height: 291px;
    background: var(--card-white);
    box-shadow: 0 2px 6px rgba(0,0,0,0.18);
    overflow: hidden;
  }
  .card--front { left: 44px; top: 233px; }
  .card--back-green { left: 628px; top: 40px; height: 292px;
    background: radial-gradient(ellipse at 50% 45%, var(--brand-green-light) 0%, #8cc84f 40%, var(--brand-green) 80%);
    display: flex; align-items: center; justify-content: center; }
  .card--back-white { left: 628px; top: 398px;
    display: flex; align-items: center; justify-content: center; }

  .brand { display: flex; align-items: center; gap: 12px;
    font-weight: 500; color: var(--brand-grey); white-space: nowrap; }
  .brand__square { width: 22px; height: 22px; background: var(--brand-green); flex: none; }
  .card--front .brand { position: absolute; left: 50px; top: 58px; font-size: 31px; }
  .card--back-white .brand { font-size: 31px; }
  .brand--reverse { color: #ffffff; font-size: 36px; }
  .brand--reverse .brand__square { background: #ffffff; width: 28px; height: 28px; }

  .front-band {
    position: absolute; left: 0; right: 0; top: 212px; bottom: 0;
    background: linear-gradient(100deg, var(--band-grey) 0%, var(--brand-green-light) 50%, var(--brand-green) 100%);
  }

  .holder { position: absolute; left: 50px; top: 186px;
    font-size: 15px; font-weight: 700; color: var(--ink-soft); }
  .holder__title { font-size: 12px; font-weight: 400; }

  .contact { position: absolute; right: 12px; top: 222px; list-style: none;
    font-size: 12px; color: var(--ink); text-align: right; line-height: 21.5px; }
  .contact li { display: flex; justify-content: flex-end; align-items: center; gap: 7px; }
  .contact svg { width: 10px; height: 10px; flex: none; }
</style>
</head>
<body>
<div class="canvas">

  <section class="card card--front" aria-label="Business card front">
    <div class="front-band" role="img" aria-label="Decorative wave band in grey and green"></div>

    <div class="brand"><span class="brand__square"></span>Northgate Developments</div>

    <p class="holder">Your Name , <span class="holder__title">Title</span></p>

    <ul class="contact">
      <li>+91 98765 43210
        <svg viewBox="0 0 10 10" aria-hidden="true"><rect x="2.5" y="0.5" width="5" height="9" rx="1" fill="var(--ink)"/><rect x="3.5" y="2" width="3" height="4" fill="#fff"/></svg></li>
      <li>+91 98765 43210
        <svg viewBox="0 0 10 10" aria-hidden="true"><rect x="2.5" y="0.5" width="5" height="3" fill="var(--ink)"/><rect x="0.5" y="3.5" width="9" height="5" rx="1" fill="var(--ink)"/></svg></li>
      <li>hello@northgatedev.com
        <svg viewBox="0 0 10 10" aria-hidden="true"><rect x="0.5" y="2" width="9" height="6" fill="var(--ink)"/><path d="M0.5,2 L5,5.5 L9.5,2" stroke="#fff" stroke-width="0.8" fill="none"/></svg></li>
    </ul>
  </section>

  <section class="card card--back-green" aria-label="Business card back, colour side">
    <div class="brand brand--reverse"><span class="brand__square"></span>Northgate</div>
  </section>

  <section class="card card--back-white" aria-label="Business card back, white side">
    <div class="brand"><span class="brand__square"></span>Northgate Developments</div>
  </section>

</div>
</body>
</html>
```